Personal training and nutrition business needs business card design

We need a business card that outlays our services and invites potential customers to join our team and take the first step to a healthier and more enjoyable life. We cater for any level of fitness and specialize in weight loss and conditioning, strength training, muscle gain and strength endurance. Whether you are just starting off or need some help getting to the next level of your journey we are here to get the job done.
We specialize in one on one or one on two personal training sessions and each program will be custom made to suit individual fitness goals of our clients

```html
<!DOCTYPE html>
<html lang="en">
<head>
<meta charset="utf-8">
<title>Stride &amp; Form — Business Card</title>
<link href="https://fonts.googleapis.com/css2?family=Exo+2:ital,wght@1,800&family=Roboto:wght@400;500;700;900&display=swap" rel="stylesheet">
<style>
  :root {
    --bg: #2a2a2b;
    --violet-deep: #563784;
    --violet: #6b3f93;
    --orchid: #9b56a0;
    --card-light: #f2f2f2;
    --ink: #151515;
    --text: #333333;
    --tag-light: #ece2f0;
  }
  * { margin: 0; padding: 0; box-sizing: border-box; }
  html, body { width: 1200px; height: 1138px; overflow: hidden; background: var(--bg); }
  body { position: relative; font-family: "Roboto", sans-serif; }

  .card { position: absolute; border-radius: 14px; overflow: hidden; }

  /* Front */
  .card-front {
    left: 274px; top: 186px; width: 623px; height: 376px;
    background: linear-gradient(115deg, var(--violet-deep) 0%, var(--violet) 45%, var(--orchid) 100%);
    color: #fff; text-align: center;
  }
  .front-name {
    position: absolute; left: 0; right: 0; top: 150px;
    font-weight: 900; font-size: 46px; letter-spacing: 2px; line-height: 1;
    color: #f4f4f4;
  }
  .front-tagline {
    position: absolute; left: 0; right: 0; top: 208px;
    font-weight: 500; font-size: 15.5px; letter-spacing: 2.2px;
    color: var(--tag-light);
  }

  /* Back */
  .card-back {
    left: 276px; top: 608px; width: 618px; height: 374px;
    background: var(--card-light);
  }
  .back-wave { position: absolute; left: 0; top: 0; width: 618px; height: 160px; }
  .holder-name {
    position: absolute; left: 32px; top: 27px;
    font-family: "Exo 2", sans-serif; font-style: italic; font-weight: 800;
    font-size: 25px; letter-spacing: 1px; color: #fff;
  }
  .holder-role {
    position: absolute; left: 31px; top: 58px;
    font-size: 15.5px; color: #f5eaf6;
  }
  .brand {
    position: absolute; left: 256px; top: 136px;
    display: flex; align-items: center; gap: 14px;
  }
  .brand-square { width: 56px; height: 56px; background: var(--violet); border-radius: 4px; }
  .brand-name {
    font-weight: 900; font-size: 30px; line-height: 1; letter-spacing: 1px; color: var(--ink);
  }
  .brand-tagline {
    position: absolute; left: 388px; top: 200px;
    font-weight: 700; font-size: 7.5px; letter-spacing: 0.6px; color: var(--orchid);
  }
  .contact-list { position: absolute; left: 32px; top: 270px; list-style: none; }
  .contact-list li {
    display: flex; align-items: center; gap: 14px;
    height: 24.5px; font-size: 16px; color: var(--text);
  }
  .contact-list svg { width: 16px; height: 16px; fill: var(--violet); }
  .web-mid { color: var(--violet); }
  .web-end { color: var(--orchid); }
  .address {
    position: absolute; right: 30px; top: 296px;
    text-align: right; font-size: 16px; line-height: 24px; color: var(--text);
  }
</style>
</head>
<body>

<section class="card card-front">
  <h1 class="front-name">STRIDE &amp; FORM</h1>
  <p class="front-tagline">PERSONAL TRAINING &nbsp;|&nbsp; NUTRITION &nbsp;|&nbsp; MOTIVATION</p>
</section>

<section class="card card-back">
  <svg class="back-wave" viewBox="0 0 618 160" aria-hidden="true">
    <defs>
      <linearGradient id="band" x1="0" y1="0" x2="1" y2="0">
        <stop offset="0" stop-color="#a45aa3"/>
        <stop offset="0.6" stop-color="#8b4b9e"/>
        <stop offset="1" stop-color="#5d3b8c"/>
      </linearGradient>
      <linearGradient id="line" x1="0" y1="0" x2="1" y2="0">
        <stop offset="0" stop-color="#a65ca4"/>
        <stop offset="1" stop-color="#5a3a8c"/>
      </linearGradient>
    </defs>
    <path d="M0,0 H618 V12 C520,16 420,24 330,58 C240,92 150,122 60,112 C30,108 12,104 0,100 Z" fill="url(#band)"/>
    <path d="M0,113 C80,150 200,138 300,92 C400,46 520,28 618,60" fill="none" stroke="url(#line)" stroke-width="7"/>
    <path d="M330,62 C420,30 520,22 618,30 V52 C540,30 440,34 330,62 Z" fill="#5d3b8c"/>
  </svg>
  <h2 class="holder-name">MARK RIVERS</h2>
  <p class="holder-role">Personal Trainer</p>

  <div class="brand">
    <span class="brand-square"></span>
    <span class="brand-name">STRIDE<br>&amp; FORM</span>
  </div>
  <p class="brand-tagline">PERSONAL TRAINING. NUTRITION. MOTIVATION</p>

  <ul class="contact-list">
    <li>
      <svg viewBox="0 0 24 24"><path d="M6.6 10.8a15 15 0 0 0 6.6 6.6l2.2-2.2a1 1 0 0 1 1-.25 11.4 11.4 0 0 0 3.6.57 1 1 0 0 1 1 1V20a1 1 0 0 1-1 1A17 17 0 0 1 3 4a1 1 0 0 1 1-1h3.5a1 1 0 0 1 1 1c0 1.25.2 2.45.57 3.57a1 1 0 0 1-.25 1z"/></svg>
      +1 (555) 240-7781
    </li>
    <li>
      <svg viewBox="0 0 24 24"><path d="M2 5h20v14H2z M4 7v.5l8 5 8-5V7l-8 5z" fill-rule="evenodd"/></svg>
      mark@strideform.com
    </li>
    <li>
      <svg viewBox="0 0 24 24"><circle cx="12" cy="12" r="9" fill="none" stroke="#6b3f93" stroke-width="2"/><path d="M3 12h18M12 3c3 3 3 15 0 18M12 3c-3 3-3 15 0 18" fill="none" stroke="#6b3f93" stroke-width="1.6"/></svg>
      <span>www.<span class="web-mid">stride</span><span class="web-end">form</span>.com</span>
    </li>
  </ul>

  <address class="address" style="font-style:normal">
    1842 Maple Ridge Lane<br>Cedar Falls Texas 75210
  </address>
</section>

</body>
</html>
```